Road Construction Company needs business cards

We would like a new business card designed for our business.

We're a road construction company based in Qld, Australia.

Can the business card please have the following information on it.

Name: Warren Halbeck
Position: General Manager
Phone: 0472 915 348
Email: Warren.halbeck@tovrin.com.au
Address: 87 Marrow Ave, Pendlebay, QLD, 4023
Website: www.tovrin.com.au

Visually we'd like the card to be professional and simple.

Attached is our logo.

Our website is www.tovrin.com.au

Target Market(s)

Men aged 25-60

Contact Information for Business Card

As listed in project description

Font styles to use
Serif

Requirements
Must have
• Large logo on back of card

```html
<!DOCTYPE html>
<html lang="en">
<head>
<meta charset="utf-8">
<title>Tovrin Road Construction – Business Card</title>
<link rel="stylesheet" href="https://fonts.googleapis.com/css2?family=Montserrat:wght@400;500;700;800&display=swap">
<style>
  :root {
    --brand-blue: #0c55a3;
    --accent-blue: #2ba3dd;
    --ink: #1e1e1e;
    --paper: #ffffff;
    --stage-top: #cfcfcf;
    --stage-bottom: #a4a4a4;
  }
  * { box-sizing: border-box; margin: 0; padding: 0; }
  html, body { width: 1200px; height: 815px; overflow: hidden; }
  body {
    background: linear-gradient(180deg, var(--stage-top), var(--stage-bottom));
    font-family: "Montserrat", sans-serif;
    position: relative;
  }
  .card {
    position: absolute;
    top: 259px;
    width: 520px;
    height: 297px;
    box-shadow: 0 14px 30px rgba(0,0,0,.28);
  }
  .card--front { left: 50px; background: var(--paper); }
  .card--back { left: 630px; background: var(--brand-blue); }

  .wordmark {
    font-weight: 800;
    text-transform: uppercase;
    line-height: 1.1;
    letter-spacing: .04em;
  }
  .card--front .wordmark {
    position: absolute;
    top: 34px;
    right: 60px;
    font-size: 22px;
    color: var(--brand-blue);
    text-align: left;
  }
  .card--back .wordmark {
    position: absolute;
    left: 0; right: 0; top: 50%;
    transform: translateY(-50%);
    font-size: 34px;
    color: var(--paper);
    text-align: center;
  }

  .identity {
    position: absolute;
    left: 34px;
    top: 148px;
  }
  .identity__name {
    font-size: 23px;
    font-weight: 700;
    color: var(--brand-blue);
    line-height: 1.1;
  }
  .identity__name span { color: var(--accent-blue); }
  .identity__role {
    font-size: 13px;
    font-weight: 500;
    color: var(--ink);
    margin-top: 3px;
  }

  .address {
    position: absolute;
    right: 34px;
    top: 160px;
    font-size: 12px;
    line-height: 1.4;
    color: var(--ink);
    text-align: left;
  }

  .divider {
    position: absolute;
    left: 34px;
    right: 34px;
    top: 206px;
    height: 1px;
    background: var(--accent-blue);
  }

  .contacts {
    position: absolute;
    left: 34px;
    top: 218px;
    list-style: none;
  }
  .contacts li {
    display: flex;
    align-items: center;
    gap: 8px;
    font-size: 12.5px;
    color: var(--ink);
    line-height: 1.55;
  }
  .contacts svg { width: 11px; height: 11px; flex: none; }
</style>
</head>
<body>

  <section class="card card--front" aria-label="Business card front">
    <div class="wordmark">Tovrin<br>Road Construction</div>

    <div class="identity">
      <p class="identity__name">Warren <span>Halbeck</span></p>
      <p class="identity__role">General Manager</p>
    </div>

    <address class="address" style="font-style:normal">
      87 Marrow Ave,<br>Pendlebay, QLD, 4023
    </address>

    <div class="divider"></div>

    <ul class="contacts">
      <li>
        <svg viewBox="0 0 12 12" aria-hidden="true"><path fill="#2ba3dd" d="M2.5 1l2 2.2-1 1.2c.7 1.5 1.9 2.7 3.3 3.4l1.2-1L10.2 9 9 10.6C5 10.4 1.6 7 1.4 3z"/></svg>
        0472 915 348
      </li>
      <li>
        <svg viewBox="0 0 12 12" aria-hidden="true"><rect x="1" y="2.5" width="10" height="7" rx="1" fill="#0c55a3"/><path d="M1.5 3l4.5 3.5L10.5 3" fill="none" stroke="#fff" stroke-width="1"/></svg>
        Warren.halbeck@tovrin.com.au
      </li>
      <li>
        <svg viewBox="0 0 12 12" aria-hidden="true"><circle cx="6" cy="6" r="5" fill="#2ba3dd"/><path d="M1 6h10M6 1c-2.5 3-2.5 7 0 10M6 1c2.5 3 2.5 7 0 10" fill="none" stroke="#fff" stroke-width=".8"/></svg>
        www.tovrin.com.au
      </li>
    </ul>
  </section>

  <section class="card card--back" aria-label="Business card back">
    <div class="wordmark">Tovrin<br>Road Construction</div>
  </section>

</body>
</html>
```